Website for International Non-Profit for Birth Parent Searching

LumaKin is a 501(c)(3) non-profit organization that helps Chinese adoptees search and reunite with birth families who were separated due the One Child Policy in China. We want to create a website that can link to an information database that allows website users to easily access information around search ads in an organized way; help connect families to professional searchers; provide resources for community support for adoptees and their families as they embark on a personal and emotional journey of finding birth family through support groups on social media and consultation/education on the searching process; and provide the opportunity for the adoptive community to give back through donations and volunteer opportunities. The final design should foster a sense of community and be easy navigable to access the multiple resources we provide to help families search for each other. We would like to see designs with red/black/white color schemes that are gentle, inviting, and family friendly to viewers. We would like to see some design layouts with Chinese themes, if possible.

```html
<!DOCTYPE html>
<html lang="en">
<head>
<meta charset="utf-8">
<title>LumaKin — International Non-Profit for Birth Parent Searching</title>
<link href="https://fonts.googleapis.com/css2?family=Nunito+Sans:wght@700;800;900&family=Roboto:wght@400;500;700&display=swap" rel="stylesheet">
<style>
:root{
  --red:#a8000b;
  --red-dark:#7e0008;
  --ink:#111111;
  --text:#444444;
  --light:#f3f3f3;
  --circle:#ececec;
  --pink:#f6e3e3;
  --white:#ffffff;
  --line:#cccccc;
}
*{box-sizing:border-box;margin:0;padding:0}
html,body{width:1200px;height:4800px;overflow:hidden;background:var(--white)}
body{position:relative;font-family:'Roboto',sans-serif;color:var(--text)}
.abs{position:absolute}
.heading{font-family:'Nunito Sans',sans-serif;font-weight:900;color:var(--ink);text-transform:uppercase;text-align:center;letter-spacing:-0.5px}

/* header */
.site-header{position:absolute;left:0;top:0;width:1200px;height:90px;background:var(--white);z-index:5}
.brand-badge{position:absolute;left:62px;top:-30px;width:185px;height:200px;border-radius:50%;background:var(--white);z-index:6;display:flex;align-items:center;justify-content:center;padding-top:36px}
.brand-name{font-family:'Roboto',sans-serif;font-weight:700;font-size:34px;color:var(--red)}
.nav{position:absolute;top:30px;left:0;width:1200px;height:24px;font-family:'Roboto',sans-serif;font-weight:700;font-size:14px;color:var(--ink)}
.nav span{position:absolute;top:3px;white-space:nowrap}
.nav .active{color:var(--red)}
.btn-donate{position:absolute;left:926px;top:-8px;width:147px;height:40px;background:var(--red);color:var(--white);display:flex;align-items:center;justify-content:center;font-size:13px;border-radius:2px}

/* hero */
.hero-photo{position:absolute;left:0;top:90px;width:1200px;height:720px;background:linear-gradient(120deg,#4f6b2c 0%,#8aa55a 35%,#c6c9a8 60%,#6d8a3a 100%)}
.hero-title{position:absolute;left:143px;top:265px;font-family:'Nunito Sans',sans-serif;font-weight:800;font-size:49px;line-height:61px;color:var(--white)}
.hero-curve{position:absolute;left:0;top:600px;width:1200px;height:260px}

.pillar{position:absolute;border-radius:50%;text-align:center;display:flex;flex-direction:column;align-items:center}
.pillar.side{width:280px;height:285px;background:var(--circle);top:665px;padding-top:28px}
.pillar.main{width:355px;height:355px;background:var(--red);top:605px;left:423px;border:7px solid var(--white);padding-top:38px;color:var(--white)}
.pillar h3{font-family:'Roboto',sans-serif;font-weight:700;font-size:15px;margin:10px 0 12px;color:var(--ink)}
.pillar.main h3{color:var(--white);font-size:18px}
.pillar p{font-size:13.5px;line-height:19px;width:200px}
.pillar.main p{color:var(--white);font-weight:500;width:250px;font-size:14px}
.pillar .arrow{margin-top:10px}
.btn-outline-white{margin-top:14px;border:2px solid var(--white);border-radius:6px;padding:9px 22px;font-size:12px;font-weight:700;color:var(--white)}

/* welcome */
.welcome-title{position:absolute;left:0;top:1036px;width:1200px;font-size:38px}
.welcome-text{position:absolute;left:180px;top:1098px;width:840px;text-align:center;font-size:15.5px;line-height:24.5px}
.btn-red{position:absolute;background:var(--red);color:var(--white);font-weight:700;font-size:13px;display:flex;align-items:center;justify-content:center;border-radius:2px;box-shadow:0 2px 4px rgba(0,0,0,.3)}

/* services */
.services{position:absolute;left:0;top:1397px;width:1200px;height:528px;background:var(--light)}
.services-title{position:absolute;left:0;top:56px;width:1200px;font-size:38px}
.service{position:absolute;top:148px;width:280px;text-align:center}
.service h4{font-family:'Roboto',sans-serif;font-weight:700;font-size:15.5px;color:var(--ink);margin-top:12px}
.service p{font-size:14px;line-height:21px;margin-top:6px}
.btn-pill{display:inline-block;margin-top:26px;border:2px solid var(--red);color:var(--red);border-radius:20px;font-size:11.5px;font-weight:700;padding:9px 18px;background:var(--white)}
.carousel-arrow{position:absolute;top:262px}

/* search banner */
.search-photo{position:absolute;left:0;top:1925px;width:1200px;height:553px;background:linear-gradient(100deg,#39401f 0%,#6b7446 30%,#9c9a7d 50%,#4d5a2b 75%,#2f3a18 100%)}
.search-card{position:absolute;left:656px;top:2033px;width:465px;height:339px;background:var(--white);padding:30px 38px;box-shadow:0 2px 8px rgba(0,0,0,.25)}
.search-card h2{font-family:'Nunito Sans',sans-serif;font-weight:900;font-size:31px;line-height:34px;color:var(--ink)}
.search-card p{font-size:14.5px;line-height:22.5px;margin-top:12px;color:#333}
.search-card .btn-red{position:static;width:216px;height:42px;margin-top:16px}

/* news */
.news-title{position:absolute;left:0;top:2540px;width:1200px;font-size:38px}
.news-card{position:absolute;width:440px;height:349px;box-shadow:0 2px 6px rgba(0,0,0,.25)}
.news-photo{width:440px;height:271px}
.news-band{width:440px;height:78px;background:var(--red);color:var(--white);font-family:'Roboto',sans-serif;font-weight:700;font-size:18px;letter-spacing:.5px;display:flex;align-items:center;justify-content:center}

/* community */
.community{position:absolute;left:0;top:3440px;width:1200px;height:435px}
.community-title{position:absolute;left:0;top:3612px;width:1200px;font-size:31px;color:var(--white)}
.field-dark{position:absolute;height:43px;border:1.5px solid rgba(255,255,255,.85);color:var(--white);font-size:14px;padding:0 22px;display:flex;align-items:center}
.btn-submit-white{position:absolute;left:814px;top:3745px;width:153px;height:43px;background:var(--white);color:var(--ink);font-weight:700;font-size:16px;display:flex;align-items:center;justify-content:center}

/* contact */
.contact{position:absolute;left:0;top:3875px;width:1200px;height:624px;background:var(--pink)}
.contact-title{position:absolute;left:0;top:3955px;width:1200px;font-size:31px}
.contact-title em{font-style:normal;color:var(--red)}
.title-rule{position:absolute;left:562px;top:4006px;width:76px;height:3px;background:var(--red)}
.field{position:absolute;background:var(--white);border:1.5px solid var(--line);font-size:11.5px;color:#333;padding:12px 17px;box-shadow:0 1px 3px rgba(0,0,0,.15)}
.btn-submit-red{position:absolute;left:523px;top:4382px;width:153px;height:37px;background:var(--red);color:var(--white);border-radius:20px;font-weight:700;font-size:13px;display:flex;align-items:center;justify-content:center}

/* footer */
.site-footer{position:absolute;left:0;top:4499px;width:1200px;height:301px;background:#050505;color:var(--white)}
.footer-brand{position:absolute;left:150px;top:120px;font-family:'Roboto',sans-serif;font-weight:700;font-size:34px;color:var(--white)}
.footer-nav{position:absolute;left:362px;top:70px;font-size:12.5px;font-weight:500}
.footer-nav span{margin-right:26px}
.footer-rule{position:absolute;left:362px;top:110px;width:678px;height:1px;background:#555}
.contact-item{position:absolute;top:140px;display:flex;align-items:center;font-size:13.5px;line-height:18px}
.contact-item .ico{width:28px;height:28px;background:var(--white);margin-right:18px;display:flex;align-items:center;justify-content:center;border-radius:2px}
.copyright{position:absolute;left:362px;top:208px;font-size:10.5px;color:#ddd}
</style>
</head>
<body>

<header class="site-header">
  <div class="brand-badge"><span class="brand-name">LumaKin</span></div>
  <nav class="nav">
    <span class="active" style="left:304px">HOME</span>
    <span style="left:375px">WHO WE ARE &nbsp;⌄</span>
    <span style="left:507px">START YOUR SEARCH</span>
    <span style="left:681px">GET INVOLVED</span>
    <span style="left:811px">RESOURCES</span>
    <span class="btn-donate">DONATE NOW</span>
    <span style="left:1094px">EN &nbsp;⌄</span>
  </nav>
</header>

<section>
  <div class="hero-photo" role="img" aria-label="Photo of a smiling family outdoors under trees, a father carrying his child on his shoulders"></div>
  <h1 class="hero-title">International<br>Non-Profit for<br>Birth Parent<br>Searching</h1>
  <svg class="hero-curve" viewBox="0 0 1200 260" preserveAspectRatio="none" aria-hidden="true">
    <path d="M0 190 C300 150 420 200 600 190 C820 175 1000 110 1200 20 L1200 260 L0 260 Z" fill="#a8000b"/>
    <path d="M0 205 C300 165 420 210 600 200 C820 185 1000 130 1200 45 L1200 260 L0 260 Z" fill="#ffffff"/>
  </svg>

  <div class="pillar side" style="left:145px">
    <svg width="64" height="60" viewBox="0 0 64 60" fill="none" stroke="#a8000b" stroke-width="3"><rect x="8" y="6" width="48" height="48" rx="4"/><path d="M18 30h28M32 18v24"/><circle cx="32" cy="30" r="8"/></svg>
    <h3>MISSION</h3>
    <p>Sed ut perspiciatis unde omnis iste natus voluptatem accuntium doloremque laudantium, totam rem aperiam, eaque</p>
    <svg class="arrow" width="26" height="22" viewBox="0 0 26 22" fill="none" stroke="#333" stroke-width="3"><path d="M2 11h20M14 3l8 8-8 8"/></svg>
  </div>
  <div class="pillar main">
    <svg width="84" height="82" viewBox="0 0 84 82" fill="none" stroke="#fff" stroke-width="3"><circle cx="42" cy="36" r="12"/><path d="M38 36h8M42 30v12"/><path d="M6 62c14-8 24-6 36 0s20 4 30-6"/><path d="M60 12l12 10-10 10"/><path d="M24 12L12 22l10 10"/></svg>
    <h3>DONATIONS</h3>
    <p>Sed ut perspiciatis unde omnis iste natus voluptatem accutium doloremque laudantium, totam rem aperiam, eaque ipsa</p>
    <span class="btn-outline-white">LEARN MORE</span>
  </div>
  <div class="pillar side" style="left:775px">
    <svg width="64" height="60" viewBox="0 0 64 60" fill="none" stroke="#a8000b" stroke-width="3"><rect x="10" y="10" width="44" height="30" rx="3"/><circle cx="32" cy="25" r="7"/><path d="M20 52h24M32 40v12"/></svg>
    <h3>VISION</h3>
    <p>Sed ut perspiciatis unde omnis iste natus voluptatem accuntium doloremque laudantium, totam rem aperiam, eaque</p>
    <svg class="arrow" width="26" height="22" viewBox="0 0 26 22" fill="none" stroke="#333" stroke-width="3"><path d="M2 11h20M14 3l8 8-8 8"/></svg>
  </div>
</section>

<section>
  <h2 class="heading welcome-title">Welcome to LumaKin</h2>
  <p class="welcome-text">Sed ut perspiciatis unde omnis iste natus error sit voluptatem accusantium doloremque laudantium, totam rem aperiam, eaque ipsa quae ab illo inventore veritatis et quasi architecto beatae vitae dicta sunt explicabo. Nemo enim ipsam voluptatem quia voluptas sit aspernatur aut odit aut fugit, sed quia consequuntur magni dolores eos qui ratione voluptatem sequi nesciunt. Neque porro quisquam est, qui dolorem ipsum quia dolor sit amet, consectetur, adipisci velit, sed quia non numquam eius modi tempora incidunt ut labore et dolore magnam aliquam quaerat voluptatem. Ut enim ad minima veniam, quis nostrum exercitationem ullam</p>
  <div class="btn-red" style="left:520px;top:1275px;width:161px;height:41px">MEET US!</div>
</section>

<section class="services">
  <h2 class="heading services-title">Our Services</h2>
  <svg class="carousel-arrow" style="left:82px" width="26" height="40" viewBox="0 0 26 40" fill="none" stroke="#bbb" stroke-width="4"><path d="M22 2L4 20l18 18"/></svg>
  <svg class="carousel-arrow" style="left:1082px" width="26" height="40" viewBox="0 0 26 40" fill="none" stroke="#bbb" stroke-width="4"><path d="M4 2l18 18L4 38"/></svg>

  <div class="service" style="left:143px">
    <svg width="125" height="125" viewBox="0 0 125 125"><circle cx="62" cy="62" r="62" fill="#a8000b"/><circle cx="86" cy="62" r="44" fill="#f3f3f3"/><circle cx="44" cy="54" r="12" fill="#f3f3f3"/><g fill="none" stroke="#a8000b" stroke-width="2.5"><path d="M70 62l16-14 16 14v20H70z"/><circle cx="86" cy="66" r="5"/></g></svg>
    <h4>FINIBUS BONORUM</h4>
    <p>Exercitation ullamco laboris nisi ut aliquip ex ea commodo consequat velit esse cillum dolore eu fugiat.</p>
    <span class="btn-pill">LEARN MORE</span>
  </div>
  <div class="service" style="left:460px">
    <svg width="125" height="125" viewBox="0 0 125 125"><circle cx="62" cy="62" r="62" fill="#a8000b"/><circle cx="86" cy="62" r="44" fill="#f3f3f3"/><circle cx="44" cy="54" r="12" fill="#f3f3f3"/><g fill="none" stroke="#a8000b" stroke-width="2.5"><circle cx="88" cy="56" r="11"/><path d="M88 67v22"/></g></svg>
    <h4>NECESSITATIBUS SAEPE</h4>
    <p>Exercitation ullamco laboris nisi ut aliquip ex ea commodo consequat velit esse cillum dolore eu fugiat.</p>
    <span class="btn-pill">LEARN MORE</span>
  </div>
  <div class="service" style="left:777px">
    <svg width="125" height="125" viewBox="0 0 125 125"><circle cx="62" cy="62" r="62" fill="#a8000b"/><circle cx="86" cy="62" r="44" fill="#f3f3f3"/><circle cx="44" cy="54" r="12" fill="#f3f3f3"/><g fill="none" stroke="#a8000b" stroke-width="2.5"><circle cx="78" cy="52" r="5"/><circle cx="96" cy="52" r="5"/><path d="M70 84V64h16v20M88 84V64h16v20"/></g></svg>
    <h4>OFFICIA DESERUNT</h4>
    <p>Exercitation ullamco laboris nisi ut aliquip ex ea commodo consequat velit esse cillum dolore eu fugiat.</p>
    <span class="btn-pill">LEARN MORE</span>
  </div>
</section>

<section>
  <div class="search-photo" role="img" aria-label="Photo of a family sitting together on the grass in a forest"></div>
  <div class="search-card">
    <h2>BIRTH PARENT<br>SEARCHING</h2>
    <p>Sed ut perspiciatis unde omnis iste natus voluptatem accusantium doloremque laudantium, totam rem aperiam, eaque ipsa quae ab illo inventore veritatis et quasi architecto beatae vitae dicta sunt explicabo. Nemo enim ipsam voluptatem quia voluptas sit aspnatur aut odit aut fugit, sed quia consequuntur</p>
    <div class="btn-red">START YOUR SEARCH</div>
  </div>
</section>

<section>
  <h2 class="heading news-title">Featured News</h2>
  <article class="news-card" style="left:147px;top:2632px">
    <div class="news-photo" role="img" aria-label="Photo of a father playing with his daughter in an autumn park" style="background:linear-gradient(135deg,#c9782c,#e7b46a 50,#8a6b45)"></div>
    <div class="news-band">JOIN THE CONVERSATION</div>
  </article>
  <article class="news-card" style="left:617px;top:2632px">
    <div class="news-photo" role="img" aria-label="Photo of a family celebrating a festive gathering at home" style="background:linear-gradient(135deg,#d9cfc4,#b0362f 55%,#6b1a14)"></div>
    <div class="news-band">UPCOMING EVENTS</div>
  </article>
  <article class="news-card" style="left:147px;top:3011px">
    <div class="news-photo" role="img" aria-label="Photo of two smiling volunteers in volunteer shirts" style="background:linear-gradient(135deg,#e8e6e1,#b6b4ae 55%,#7c8f5a)"></div>
    <div class="news-band">VOLUNTEER OPPORTUNITIES</div>
  </article>
  <article class="news-card" style="left:617px;top:3011px">
    <div class="news-photo" role="img" aria-label="Photo of a multi-generation family walking together in a sunny park" style="background:linear-gradient(180deg,#9aa57a,#6f8a3c 60%,#4f6c25)"></div>
    <div class="news-band">SUCCESS STORY</div>
  </article>
</section>

<section>
  <svg class="community" viewBox="0 0 1200 435" preserveAspectRatio="none" role="img" aria-label="Red-toned photo of a child looking up, used as background">
    <defs><linearGradient id="redwash" x1="0" y1="0" x2="1" y2="1"><stop offset="0" stop-color="#6e0007"/><stop offset=".5" stop-color="#a3141b"/><stop offset="1" stop-color="#8a0a10"/></linearGradient></defs>
    <path d="M0 30 C300 -5 560 60 800 45 C980 35 1100 40 1200 90 L1200 435 L0 435 Z" fill="#444"/>
    <path d="M0 45 C300 12 560 75 800 60 C980 50 1100 55 1200 105 L1200 435 L0 435 Z" fill="url(#redwash)"/>
  </svg>
  <h2 class="heading community-title">Join the Community! Get Email Updates</h2>
  <div class="field-dark" style="left:231px;top:3685px;width:361px">First Name</div>
  <div class="field-dark" style="left:607px;top:3685px;width:360px">Last Name</div>
  <div class="field-dark" style="left:231px;top:3745px;width:583px">Email address</div>
  <div class="btn-submit-white">SUBMIT</div>
</section>

<section class="contact"></section>
<h2 class="heading contact-title">Get <em>in Touch</em></h2>
<div class="title-rule"></div>
<div class="field" style="left:227px;top:4056px;width:369px;height:41px">First Name</div>
<div class="field" style="left:605px;top:4056px;width:367px;height:41px">Last Name</div>
<div class="field" style="left:227px;top:4110px;width:369px;height:41px">Email address</div>
<div class="field" style="left:605px;top:4110px;width:367px;height:41px">Address</div>
<div class="field" style="left:227px;top:4166px;width:745px;height:56px">Phone number</div>
<div class="field" style="left:227px;top:4238px;width:745px;height:112px">Reason for inquiry</div>
<div class="btn-submit-red">SUBMIT</div>

<footer class="site-footer">
  <div class="footer-brand">LumaKin</div>
  <div class="footer-nav"><span>HOME</span><span>WHO WE ARE</span><span>OUR SERVICES</span><span>GET INVOLVED</span><span>TOOLS AND RESOURCES</span><span>CONTACT US</span></div>
  <div class="footer-rule"></div>
  <div class="contact-item" style="left:362px">
    <span class="ico"><svg width="16" height="16" viewBox="0 0 16 16"><path d="M3 1l3 3-2 2c1 2 3 4 5 5l2-2 3 3-2 3C7 15 1 9 1 3z" fill="#a8000b"/></svg></span>
    <span>Phone:<br>555-014-2276</span>
  </div>
  <div class="contact-item" style="left:530px">
    <span class="ico"><svg width="14" height="18" viewBox="0 0 14 18"><path d="M7 1a6 6 0 0 1 6 6c0 4-6 10-6 10S1 11 1 7a6 6 0 0 1 6-6z" fill="#a8000b"/><circle cx="7" cy="7" r="2.2" fill="#fff"/></svg></span>
    <span>2200 Maple Crest Road,<br>4B, Larkfield, CO 80100</span>
  </div>
  <div class="contact-item" style="left:780px">
    <span class="ico"><svg width="18" height="14" viewBox="0 0 18 14"><rect x="1" y="1" width="16" height="12" fill="#a8000b"/><path d="M1 1l8 7 8-7" fill="none" stroke="#fff" stroke-width="1.5"/></svg></span>
    <span>Email:<br>hello@lumakin.org</span>
  </div>
  <div class="copyright">© COPYRIGHTS 2021 LUMAKIN &nbsp; | &nbsp; ALL RIGHTS RESERVED</div>
</footer>

</body>
</html>
```